Brindle Yard Care. The best in the biz

I run a lawn care service that offers full service mowing. 100% satisfaction guarantee. Fast, Friendly, quality service "I am your lawns best friend" I cut residential lawns. I offer a mow package that includes trimming, edging and clean up. Prices very from 20 dollars to 75. I want my logo to stand out. Free estimates

Target Market(s)

Home owners

Industry/Entity Type

Landscaping

Contact Information for Business Card

555-812-4473 tomvale48@quillmail.net Derek. Brindle Yard care

Colors
f37122
9bcb3c
cadf82

Requirements
Must have
• Company name.
• Phone number
• Email
• My services
• images
Nice to have
• A sun that is growing grass.
Should not have
• Incorrect information

```html
<!DOCTYPE html>
<html lang="en">
<head>
<meta charset="utf-8">
<title>Brindle Yard Care – Business Card</title>
<link rel="stylesheet" href="https://fonts.googleapis.com/css2?family=Open+Sans:wght@400;600;700&display=swap">
<style>
  :root {
    --orange: #f08a24;
    --orange-deep: #e57a17;
    --orange-text: #f37122;
    --green: #1e9a3f;
    --white: #ffffff;
    --ink: #2b2b2b;
    --backdrop: #ecebe8;
  }
  * { box-sizing: border-box; margin: 0; padding: 0; }
  html, body {
    width: 1200px; height: 900px; overflow: hidden;
    background: var(--backdrop);
    font-family: "Open Sans", Arial, sans-serif;
  }
  .canvas {
    position: relative; width: 1200px; height: 900px;
  }
  .card {
    position: absolute; width: 700px; height: 400px;
    left: 250px; overflow: hidden;
    box-shadow: 0 6px 18px rgba(0,0,0,.18);
  }
  .card--front { top: 40px; background: var(--orange); }
  .card--back { top: 460px; background: var(--white); }

  /* Front */
  .front__brand {
    position: absolute; top: 70px; left: 0; right: 0;
    text-align: center; color: var(--white);
    font-weight: 700; font-size: 44px; letter-spacing: 1px;
  }
  .front__promise {
    position: absolute; top: 178px; left: 0; right: 0;
    text-align: center; color: var(--white);
  }
  .front__guarantee { font-size: 24px; font-weight: 700; }
  .front__values { font-size: 20px; font-weight: 600; margin-top: 8px; word-spacing: 2px; }
  .front__rule {
    position: absolute; top: 276px; left: 0; right: 0; height: 6px;
    background: var(--orange-deep);
  }
  .front__band {
    position: absolute; top: 282px; left: 0; right: 0; height: 84px;
    background: var(--white);
    display: flex; align-items: flex-start; justify-content: center;
  }
  .front__tagline {
    margin-top: 6px; width: 100%; text-align: center;
    background: var(--white); color: var(--orange-text);
    font-size: 24px; font-weight: 400; padding-top: 6px;
    border-top: 3px solid var(--orange);
  }
  .front__base {
    position: absolute; bottom: 0; left: 0; right: 0; height: 34px;
    background: var(--orange);
  }

  /* Back */
  .back__contact {
    position: absolute; top: 46px; left: 430px;
  }
  .back__name {
    color: var(--orange-text); font-weight: 700; font-size: 22px;
    margin-bottom: 16px;
  }
  .back__line {
    display: flex; align-items: center; gap: 8px;
    font-size: 16px; color: var(--ink); margin-bottom: 8px;
  }
  .back__line svg { width: 14px; height: 14px; flex: none; }
  .back__logo {
    position: absolute; right: 50px; bottom: 60px;
    display: flex; align-items: center; gap: 14px;
  }
  .back__logo-dot {
    width: 30px; height: 30px; border-radius: 50%;
    background: var(--orange-text);
  }
  .back__brand {
    color: var(--green); font-weight: 700; font-size: 42px;
  }
</style>
</head>
<body>
<main class="canvas">
  <section class="card card--front" aria-label="Card front">
    <div class="front__brand">Brindle Yard Care</div>
    <div class="front__promise">
      <p class="front__guarantee">100% satisfaction guarantee.</p>
      <p class="front__values">Fast | Friendly | Quality Service</p>
    </div>
    <div class="front__rule"></div>
    <div class="front__band">
      <p class="front__tagline">I am your lawns best friend</p>
    </div>
    <div class="front__base"></div>
  </section>

  <section class="card card--back" aria-label="Card back">
    <div class="back__contact">
      <p class="back__name">Derek</p>
      <p class="back__line">
        <svg viewBox="0 0 16 16" aria-hidden="true"><path fill="#f37122" d="M3.6 1.5l2.3 2.6-1.3 1.8c.9 2 2.5 3.6 4.5 4.5l1.8-1.3 2.6 2.3-1.3 2.2C7.4 15.4.6 8.6 1.4 2.8z"/></svg>
        555-812-4473
      </p>
      <p class="back__line">
        <svg viewBox="0 0 16 16" aria-hidden="true"><rect x="1" y="3" width="14" height="10" fill="#f37122"/><path d="M1 3l7 6 7-6" fill="none" stroke="#fff" stroke-width="1.4"/></svg>
        tomvale48@quillmail.net
      </p>
    </div>
    <div class="back__logo">
      <span class="back__logo-dot" aria-hidden="true"></span>
      <span class="back__brand">Brindle Yard Care</span>
    </div>
  </section>
</main>
</body>
</html>
```